This book will apply the 12 Steps to gaming addiction, also known as video game addiction. The primary purpose of the book is to provide an effective solution for this new type of addiction. The solution is based on the rich and successful concepts of traditional twelve-step programs like RQ.

The title on the cover will be "Nine Doors Out of the Endless Level" and "by Peter Halvorn". A subtitle can be used if it works in your design of "A Practical Path Back from Compulsive Screen Play". Cover will be for a 6" x 9" book approximately 110 pages in length.

Some back cover text including some review quotes and an author bio are in the attached Word doc. There is also an author photo attached for for the back cover.

Requirements
Must have
• For the cover design it could be stylized, or an image, a partial image, or whatever. I am open to suggestions. Think about what would be noticed by a person searching for help with moderating their video game use, or by the parents or loved ones of problem gamers. Something contemporary and eye catching.

```html
<!DOCTYPE html>
<html lang="en">
<head>
<meta charset="utf-8">
<title>Nine Doors Out of the Endless Level — Cover Spread</title>
<link rel="stylesheet" href="https://fonts.googleapis.com/css2?family=Poppins:wght@400;500;600;700&family=Teko:wght@300;400;500;600&display=swap">
<style>
  :root {
    --page-bg: #ffffff;
    --ember: #ff8a5c;
    --ember-light: #ffb08a;
    --violet: #8e8ff0;
    --lavender: #a9b5ea;
    --ink: #ffffff;
    --credit: #8fa2d8;
    --rule: rgba(255,255,255,0.28);
  }
  * { box-sizing: border-box; margin: 0; padding: 0; }
  html, body {
    width: 1200px; height: 1000px; overflow: hidden;
    background: var(--page-bg);
    font-family: "Poppins", sans-serif;
  }
  .spread {
    position: absolute; left: 106px; top: 158px;
    width: 988px; height: 684px;
    background:
      radial-gradient(circle at 22% 26%, rgba(70,90,200,0.35), transparent 18%),
      radial-gradient(circle at 8% 40%, rgba(160,40,60,0.30), transparent 14%),
      radial-gradient(circle at 46% 54%, rgba(150,40,60,0.28), transparent 12%),
      radial-gradient(circle at 30% 70%, rgba(40,80,190,0.30), transparent 20%),
      linear-gradient(180deg, #07080f 0%, #0a0f24 60%, #0a1638 100%);
    color: var(--ink);
    overflow: hidden;
  }

  /* Back cover */
  .back {
    position: absolute; left: 0; top: 0; width: 452px; height: 100%;
    padding: 34px 45px 0 45px;
    display: flex; flex-direction: column;
  }
  .praise-heading {
    font-family: "Teko", sans-serif; font-weight: 500; font-size: 19px;
    letter-spacing: 0.6px; text-transform: uppercase; margin-bottom: 10px; line-height: 1.1;
  }
  .praise-heading .accent { color: var(--ember); }
  .praise-heading .accent-blue { color: var(--violet); }
  .review { font-size: 7.8px; font-weight: 500; line-height: 1.42; margin-bottom: 12px; }
  .review .credit { display: block; font-size: 7.2px; font-weight: 400; }
  .review .credit .name { color: var(--credit); font-weight: 600; text-transform: uppercase; }
  .divider { height: 1px; background: var(--rule); margin: 4px 0 13px; }
  .blurb p { font-size: 7.8px; line-height: 1.45; margin-bottom: 9px; }
  .author-band {
    margin: 6px -45px 0;
    background: linear-gradient(90deg, rgba(10,24,60,0.85), rgba(12,36,90,0.6));
    display: flex; gap: 16px; padding: 14px 45px;
  }
  .author-photo {
    flex: 0 0 62px; height: 74px;
    background: linear-gradient(160deg, #cbb8a6, #6d5e57 60%, #2a3550);
  }
  .author-bio { font-size: 7.8px; line-height: 1.55; }
  .author-bio .name { color: var(--ember); font-weight: 600; text-transform: uppercase; }

  /* Spine */
  .spine { position: absolute; left: 452px; top: 0; width: 75px; height: 100%; }
  .spine-title {
    position: absolute; left: 50%; top: 24px;
    writing-mode: vertical-rl; transform: translateX(-50%);
    font-family: "Teko", sans-serif; font-weight: 400; font-size: 17px;
    letter-spacing: 4.6px; text-transform: uppercase;
    background: linear-gradient(180deg, var(--ember-light), var(--violet));
    -webkit-background-clip: text; background-clip: text; color: transparent;
  }
  .spine-author {
    position: absolute; left: 50%; bottom: 26px;
    writing-mode: vertical-rl; transform: translateX(-50%);
    font-family: "Teko", sans-serif; font-weight: 500; font-size: 17px;
    letter-spacing: 3px; color: var(--ember); text-transform: uppercase;
  }

  /* Front cover */
  .front { position: absolute; left: 527px; top: 0; width: 461px; height: 100%; }
  .front-art {
    position: absolute; left: 0; top: 390px; width: 100%; height: 294px;
    background:
      radial-gradient(ellipse at 62% 45%, rgba(111,211,255,0.75), transparent 38%),
      radial-gradient(ellipse at 40% 70%, rgba(47,142,232,0.55), transparent 45%),
      radial-gradient(circle at 88% 60%, rgba(200,60,80,0.45), transparent 22%),
      radial-gradient(circle at 12% 30%, rgba(160,60,90,0.35), transparent 20%),
      linear-gradient(180deg, rgba(10,20,50,0), #0c2a70 70%, #0a1c50);
  }
  .title-block { position: absolute; left: 0; top: 40px; width: 100%; height: 240px; }
  .title-lines { position: absolute; left: 0; top: 0; width: 461px; height: 240px; }
  .title-left, .title-right {
    position: absolute; font-family: "Teko", sans-serif; font-weight: 600; line-height: 0.85;
  }
  .title-left { left: 40px; top: 44px; width: 140px; }
  .title-left span {
    display: block;
    background: linear-gradient(180deg, var(--ember), var(--ember-light));
    -webkit-background-clip: text; background-clip: text; color: transparent;
  }
  .title-left .nine { font-size: 96px; }
  .title-left .doors { font-size: 60px; margin-top: 4px; }
  .title-right { left: 214px; top: 36px; font-weight: 500; }
  .title-right .of { display: block; font-size: 40px; color: var(--ink); }
  .title-right .word {
    display: block; font-size: 76px;
    background: linear-gradient(90deg, var(--violet), var(--ember-light));
    -webkit-background-clip: text; background-clip: text; color: transparent;
  }
  .front-quote {
    position: absolute; left: 36px; top: 318px; width: 398px; text-align: center;
    font-size: 12px; font-weight: 600; line-height: 1.38;
  }
  .front-credit {
    position: absolute; left: 36px; top: 370px; width: 398px; text-align: center;
    font-size: 9.6px; line-height: 1.5;
  }
  .front-credit .name { color: var(--lavender); font-weight: 600; text-transform: uppercase; }
  .front-author {
    position: absolute; left: 0; bottom: 22px; width: 100%; text-align: center;
    font-family: "Teko", sans-serif; font-weight: 500; font-size: 50px;
    letter-spacing: 8px; text-transform: uppercase; line-height: 1; white-space: nowrap;
  }
</style>
</head>
<body>
<main class="spread">
  <section class="back">
    <h2 class="praise-heading">Praise for <span class="accent">Nine Doors</span> <span class="accent-blue">Out of the Endless Level</span></h2>
    <blockquote class="review">“A must-read for anyone who is addicted to or thinks they may have a problem with digital gaming. This eloquent work will also be useful to academics and clinicians exploring potential solutions. The author recognizes the similarities between gaming addiction and other addictions, and logically applies one of the most effective known solutions for addiction - The Twelve Steps.”
      <span class="credit"><span class="name">Dale Whitcombe</span>, Noted Interventionist and Keynote Speaker</span></blockquote>
    <blockquote class="review">“If you suffer from digital gaming addiction, I strongly encourage you to use this book as your road map to get you back to the real world.”
      <span class="credit"><span class="name">Martin Ostrand</span>, Founder of Online Habits Review.</span></blockquote>
    <blockquote class="review">“As a high school teacher for 24 years, husband, father, coach, and 12-Step member, I can assure you that this book will transform the life of anyone who is addicted to video games. Well written, easy to understand, and a wonderful book that will provide you with a clear road map to recovery, and this includes teenagers, a group I have been working with in the classroom for decades.”
      <span class="credit"><span class="name">Victor Alden, Fair Harbor</span>, CA High School Teacher.</span></blockquote>
    <div class="divider"></div>
    <div class="blurb">
      <p>A Practical Path Back from Compulsive Screen Play (aka Video Game Addiction) based on the rich and successful tradition of the Twelve Steps.</p>
      <p>Addiction to Digital Gaming is a new and troubling phenomenon that has burst upon an unprepared society with alarming speed. Many people crave the use of Digital Games in a strikingly similar way to any other addict. Digital Games are a complex software and hardware system that have been designed to promote continued and progressive usage. This sophisticated technology clearly feeds on natural addictive tendencies.</p>
      <p>THE 12 STEPS are one of the most effective methods for treating addiction in human history. Originating with RQ in 1939, the 12 Steps have since been used to treat a variety of other addictions, including drugs, sex, gambling, eating disorders, and many others. Now in this groundbreaking work the 12 Steps are applied to the complex and evolving contemporary phenomenon of Digital Gaming Addiction.</p>
    </div>
    <div class="author-band">
      <div class="author-photo" role="img" aria-label="Portrait photo of the author"></div>
      <p class="author-bio"><span class="name">Peter Halvorn</span> is a Technology Consultant and Writer with many years of professional coding and consulting experience. He also struggled with addiction to drugs and alcohol and is now clean and sober in a Twelve-Step program for over 17 years. This unique combination of 12-Step experience and technology expertise led him to create Nine Doors Out of the Endless Level.</p>
    </div>
  </section>

  <section class="spine">
    <span class="spine-title">Nine Doors Out of the Endless Level</span>
    <span class="spine-author">Peter Halvorn</span>
  </section>

  <section class="front">
    <div class="front-art" role="img" aria-label="Glowing blue game controller photo with soft coloured bokeh lights"></div>
    <div class="title-block">
      <svg class="title-lines" viewBox="0 0 461 240" aria-hidden="true">
        <g fill="none" stroke="#8e8ff0" stroke-width="1.4">
          <polyline points="40,30 196,30 196,226"/>
          <line x1="196" y1="62" x2="202" y2="62"/>
        </g>
        <circle cx="203" cy="62" r="5" fill="#8e8ff0"/>
        <circle cx="196" cy="228" r="5" fill="#8e8ff0"/>
      </svg>
      <div class="title-left" aria-hidden="true">
        <span class="nine">NINE</span>
        <span class="doors">DOORS</span>
      </div>
      <h1 class="title-right">
        <span class="of">OUT OF THE</span>
        <span class="word">ENDLESS</span>
        <span class="word">LEVEL</span>
      </h1>
    </div>
    <p class="front-quote">“A must-read for anyone who is addicted to or thinks they may have a problem with digital gaming...”</p>
    <p class="front-credit"><span class="name">Dale Whitcombe</span><br>Noted Interventionist and Keynote Speaker</p>
    <p class="front-author">Peter Halvorn</p>
  </section>
</main>
</body>
</html>
```